Catalogue Design Project

We need a catalog design for a new private university called Redwell Institute Bayshore (see website www.rwi-bs.org). The catalog should be about 30 pages maximum and will include items such as General Information, Academic schedule, department descriptions, program descriptions, course descriptions, school policies, student services, admissions, San diego Lifestyle, etc.
I will provide the text but I need a professional design with regard to page layouts. I have provided some examples.
Ok, i posted the catalog content, just missing course descriptions.
Target Market(s)
Young Professionals, Foreign Students
Industry/Entity Type
University
Look and feel
Each slider illustrates characteristics of the customer's brand and the style your logo design should communicate.

```html
<!DOCTYPE html>
<html lang="en">
<head>
<meta charset="utf-8">
<title>Academic Programs – Certificate Programs</title>
<link href="https://fonts.googleapis.com/css2?family=Carlito:ital,wght@0,400;0,700;1,400&display=swap" rel="stylesheet">
<style>
  :root {
    --ink: #1a1a1a;
    --navy: #2a5a8e;
    --navy-dark: #1f4674;
    --grey-dot: #a9a9a9;
    --rule: #9aa3ad;
    --footer-grey: #8a8a8a;
    --paper: #ffffff;
    --book-warm: #e3d7bf;
    --book-shadow: #b9a888;
  }
  * { margin: 0; padding: 0; box-sizing: border-box; }
  html, body { width: 927px; height: 1200px; overflow: hidden; background: var(--paper); }
  body { font-family: "Carlito", "Calibri", sans-serif; color: var(--ink); }
  .page { position: relative; width: 927px; height: 1200px; overflow: hidden; }

  .header-photo {
    position: absolute; right: 0; top: 0; width: 400px; height: 152px;
    background: linear-gradient(90deg, rgba(255,255,255,1) 0%, rgba(241,235,222,0.7) 30%, var(--book-warm) 65%, var(--book-shadow) 100%);
  }
  .brand-ornament {
    position: absolute; left: 58px; top: 58px; width: 126px; height: 32px;
    background: linear-gradient(90deg, var(--grey-dot) 0%, #b8bcc2 60%, var(--navy) 100%);
    border-radius: 8px;
  }

  .section-title {
    position: absolute; left: 307px; top: 94px;
    font-size: 31px; letter-spacing: 0.5px; color: var(--ink);
  }
  .header-rule { position: absolute; left: 303px; right: 0; top: 131px; height: 2px; background: var(--rule); }
  .header-bar { position: absolute; left: 303px; top: 133px; width: 318px; height: 15px; background: var(--navy); }
  .header-base { position: absolute; left: 0; right: 0; top: 151px; height: 1px; background: var(--rule); }

  .program-tab {
    position: absolute; left: 0; top: 177px; width: 426px; height: 43px;
    background: linear-gradient(180deg, var(--navy) 0%, var(--navy-dark) 100%);
    border-radius: 0 12px 12px 0;
    box-shadow: 2px 2px 0 #173a60;
    color: #fff; font-size: 30px; line-height: 43px; padding-left: 62px; letter-spacing: 0.3px;
  }

  .program-name {
    position: absolute; left: 0; right: 0; top: 245px;
    text-align: center; font-weight: 700; font-size: 26px;
  }
  .content { position: absolute; left: 79px; width: 803px; font-size: 20.6px; }
  .intro { top: 282px; line-height: 36.4px; text-align: justify; }
  .facts { top: 500px; line-height: 36.4px; }
  .facts strong { font-weight: 700; }
  .course-list { line-height: 27.3px; }
  .course-list h3 { font-weight: 400; font-size: 20.6px; text-decoration: underline; }
  .course-list ul { list-style: none; }
  .required { top: 604px; }
  .electives { top: 777px; }
  .outcome { top: 968px; line-height: 27.3px; text-align: justify; }
  .outcome h3 { font-weight: 400; font-size: 20.6px; text-decoration: underline; }

  .footer-rule { position: absolute; left: 0; right: 0; top: 1156px; height: 1px; background: var(--rule); }
  .folio {
    position: absolute; right: 36px; top: 1170px;
    font-size: 13.5px; color: var(--footer-grey); letter-spacing: 0.6px;
  }
</style>
</head>
<body>
<div class="page">
  <div class="header-photo" role="img" aria-label="Open antique book lying on a desk, soft warm tones fading into white"></div>

  <div class="brand-ornament" role="img" aria-label="Decorative brand ornament of grey and blue dots"></div>

  <div class="section-title">ACADEMIC PROGRAMS</div>
  <div class="header-rule"></div>
  <div class="header-bar"></div>
  <div class="header-base"></div>

  <div class="program-tab">CERTIFICATE PROGRAMS</div>

  <h2 class="program-name">E-Commerce/Online Marketing Certificate</h2>

  <p class="content intro">The E-Commerce Certificate program is created for students wanting to develop the skills necessary to produce successful commerce sites for business. Students will have the opportunity to design actual e-commerce sites, implement them, and after examination evaluate their strengths and weaknesses. Coursework will involve an overview of marketing, legal ramifications of online processing, and the trained use of the latest technologies in both hardware and software.</p>

  <div class="content facts">
    <p><strong>Hours:</strong> 6 hours per week</p>
    <p><strong>Length:</strong> 8 weeks per course</p>
  </div>

  <div class="content course-list required">
    <h3>Required Courses:</h3>
    <ul>
      <li>MKT 603 Internet Advertising Solutions</li>
      <li>MKT 606 E-Commerce</li>
      <li>COMP 600 Website Creation</li>
      <li>BUS 610 Business Legalities</li>
    </ul>
  </div>

  <div class="content course-list electives">
    <h3>Elective Courses: (Choose 1)</h3>
    <ul>
      <li>MKT 602 Marketing Research</li>
      <li>MKT 607 Marketing Internship</li>
      <li>BUS 600 Starting Your Own Business</li>
      <li>COMP 601 Internet Technology</li>
      <li>COMP 602 Introduction to Java Script</li>
    </ul>
  </div>

  <div class="content outcome">
    <h3>Learning Outcome:</h3>
    <p>Graduates will be able to create a professional website, use search engine optimization, and make their products as visible as possible to the target market and therefore produce a successful business online.</p>
  </div>

  <div class="footer-rule"></div>
  <div class="folio">13::: REDWELL INSTITUTE</div>
</div>
</body>
</html>
```